Wordpress Design Project - LumaFernSites

I would like our existing old website at www.lumafernsites.example to be redesigned to a more modern attractive site using Wordpress, a total of 5 web pages. And also installed onto our new web hosting site. Please visit the existing website using Microsoft Internet explorer to see the content.
The new site must be compatible with all popular web browsers and mobile devices (if possible).
There should be a contact button available on each page with an associated form in case an interested person wants to contact us. This form must be spam proof not allowing automated crawlers from activating it.
Updates

There are only 5 pages web pages to this LumaFernSites project.

Industry/Entity Type

Internet

```html
<!DOCTYPE html>
<html lang="en">
<head>
<meta charset="utf-8">
<title>LumaFernSites</title>
<link href="https://fonts.googleapis.com/css2?family=Oswald:wght@400;500&family=Source+Sans+3:ital,wght@0,400;0,600;1,400&display=swap" rel="stylesheet">
<style>
:root{
  --blue:#1160b3;
  --blue-dark:#0b4f98;
  --blue-light:#2b7bcb;
  --link:#1a64b5;
  --text:#2f2f2f;
  --muted:#666;
  --page:#eef0f3;
  --white:#fff;
  --red:#c8141b;
  --line:#cfd3d8;
}
*{box-sizing:border-box;margin:0;padding:0}
html,body{width:1050px;height:1200px;overflow:hidden}
body{position:relative;background:linear-gradient(#fafbfc,#eceef1 20%,#eef0f3);font-family:"Source Sans 3",sans-serif;color:var(--text)}
.abs{position:absolute}
.header-top{left:0;top:0;width:1050px;height:101px;border-top:2px solid var(--blue)}
.brand{left:105px;top:34px;display:flex;align-items:center;gap:10px}
.brand-dot{width:30px;height:30px;border-radius:50%;background:var(--blue)}
.brand-name{font-family:"Source Sans 3",sans-serif;font-weight:600;font-size:27px;color:var(--blue)}
.phone{left:621px;top:26px;display:flex;align-items:center;gap:10px;font-size:12px;color:#333}
.phone strong{font-weight:400;font-size:17px;color:var(--blue)}
.email{left:625px;top:66px;display:flex;align-items:center;gap:12px;font-size:12px;color:#444}
.btn-contact{left:836px;top:35px;width:118px;height:28px;background:linear-gradient(#2c8be0,var(--blue-dark));border:1px solid #0a4a90;border-radius:2px;color:#fff;font-family:"Oswald",sans-serif;font-size:16px;text-align:center;line-height:26px;box-shadow:0 0 0 2px #fff,0 1px 3px rgba(0,0,0,.3)}
.nav{left:0;top:102px;width:1050px;height:49px;background:linear-gradient(var(--blue),var(--blue-dark));border-bottom:2px solid #d5dbe2}
.nav-item{position:absolute;top:0;height:49px;line-height:49px;font-family:"Oswald",sans-serif;font-size:12.5px;color:#fff;white-space:nowrap}
.nav-item.active{background:var(--blue-light);padding:0 10px;left:103px;width:130px;text-align:center;font-size:12px}
.nav-sep{position:absolute;top:0;width:1px;height:49px;background:#3f86cf}
.search{left:808px;top:115px;width:146px;height:21px;background:#fff;border:1px solid #bcc8d6;font-size:10px;font-style:italic;color:#999;padding:4px 10px}
.slider{left:101px;top:165px;width:851px;height:317px;border:1px solid #c8c8c8;background:linear-gradient(100deg,#c9c3ba 0%,#7b7670 30%,#2a2b2f 45%,#3b86c9 55%,#2a2b2f 65%,#bfb7a8 80%,#c46e2a 100%);box-shadow:0 8px 10px -6px rgba(0,0,0,.35)}
.caption{left:101px;top:263px;width:315px;height:131px;background:rgba(40,40,40,.78);padding:12px 14px;color:#fff}
.caption h2{font-family:"Oswald",sans-serif;font-weight:400;font-size:18px;padding-bottom:5px;border-bottom:1px solid #ddd;width:270px;margin-bottom:8px}
.caption p{font-size:11.5px;line-height:17.5px}
.dots{left:880px;top:462px;display:flex;gap:4px}
.dots span{width:12px;height:10px;background:#555}
.dots span:first-child{background:var(--blue-light)}
.panel{background:linear-gradient(#1f72c6,var(--blue-dark));border-radius:8px;border:2px solid #d5dde7;box-shadow:2px 3px 4px rgba(0,0,0,.25)}
.quick{left:101px;top:508px;width:226px;height:400px}
.quick-title{left:156px;top:520px;font-family:"Oswald",sans-serif;font-size:18px;color:#fff}
.quick-rule{left:107px;top:549px;width:214px;height:1px;background:#5d9ad6}
.env{left:110px;top:515px}
.field{position:absolute;left:117px;width:194px;height:27px;background:#fff;border:1px solid #9bb9d9;font-size:10px;font-style:italic;color:#888;padding:7px 13px}
.captcha{left:117px;top:775px;width:195px;height:80px;background:#222;border-radius:3px;padding:3px}
.captcha-words{height:38px;background:#f2f2f2}
.captcha-entry{margin-top:5px;margin-left:8px;width:106px;height:26px;font-size:7px;color:#bbb}
.captcha-entry div{margin-top:4px;height:11px;background:#fff}
.btn-submit{left:241px;top:869px;width:70px;height:25px;border:1px solid #fff;border-radius:13px;background:var(--blue-dark);color:#fff;font-style:italic;font-weight:600;font-size:14px;text-align:center;line-height:23px}
.signup{left:101px;top:928px;width:226px;height:168px;border-radius:3px}
.signup-title{left:126px;top:946px;font-size:16px;font-weight:600;color:#fff}
.signup-text{left:111px;top:974px;width:205px;font-size:10px;line-height:15px;color:#fff}
.signup-input{left:110px;top:1012px;width:206px;height:25px;background:#fff;border:1px solid #ccc;font-size:9.5px;font-style:italic;color:#888;padding:6px 10px}
.btn-subscribe{left:241px;top:1054px;width:75px;height:23px;background:var(--red);border-radius:2px;color:#fff;font-size:12px;font-weight:600;text-align:center;line-height:23px}
.main{left:353px;top:514px;width:601px;height:588px;background:#fff;border:1px solid #d8d8d8;border-radius:4px;box-shadow:0 0 8px rgba(0,0,0,.08)}
.welcome-title{left:382px;top:533px;font-family:"Oswald",sans-serif;font-size:17px;color:var(--blue-dark)}
.welcome-title span{color:var(--blue-light)}
.welcome-img{left:379px;top:575px;width:155px;height:158px;background:linear-gradient(#f4f4f4,#c9cdd2 55%,#3a3a3a 80%,#e9e9e9)}
.welcome-text{left:540px;top:589px;width:398px;font-size:12px;line-height:15.8px;color:#333;text-align:justify}
.welcome-text p{margin-bottom:15.5px}
.welcome-text a,.more-text a{color:var(--link);text-decoration:none}
.more-text{left:381px;top:750px;width:554px;font-size:12px;line-height:15.8px;color:#333}
.btn-more{background:var(--blue);color:#fff;font-family:"Oswald",sans-serif;font-size:12.5px;text-align:center}
.btn-more.one{left:864px;top:851px;width:71px;height:28px;line-height:28px}
.btn-more.two{left:499px;top:1033px;width:70px;height:28px;line-height:28px}
.sub-title{font-family:"Oswald",sans-serif;font-size:15.5px;color:#444;padding-bottom:4px;border-bottom:1px solid var(--line)}
.why-title{left:388px;top:900px;width:231px}
.ip-title{left:686px;top:900px;width:231px}
.why-img{left:388px;top:941px;width:98px;height:78px;background:linear-gradient(#3a3d44,#1c1e23)}
.why-text{left:497px;top:941px;width:125px;font-size:10px;line-height:15.8px;color:#555}
.ip-list{left:686px;top:933px;list-style:none}
.ip-list li{height:29px;display:flex;align-items:center;gap:9px;font-family:"Oswald",sans-serif;font-size:12px;color:var(--link)}
.ip-list li::before{content:"›";color:#555;font-size:13px}
.footer{left:0;top:1123px;width:1050px;height:77px;background:linear-gradient(var(--blue),#2565ad)}
.social{left:108px;top:1146px;display:flex;gap:10px}
.social span{width:23px;height:23px;border-radius:2px;border:1px solid rgba(255,255,255,.5)}
.copy{left:673px;top:1146px;width:280px;text-align:right;font-size:10.5px;color:#dbe6f3;white-space:nowrap}
</style>
</head>
<body>
<header>
  <div class="abs header-top"></div>
  <div class="abs brand"><span class="brand-dot"></span><span class="brand-name">LumaFernSites</span></div>
  <div class="abs phone">
    <svg width="26" height="20" viewBox="0 0 26 20"><path d="M3 4c2-3 6-3 7 0l-2 3c2 3 4 5 7 6l2-2c3 0 4 3 2 5-6 4-18-5-16-12z" fill="#444"/></svg>
    <span>Toll Free <strong>1.888.555.0142</strong></span>
  </div>
  <div class="abs email">
    <svg width="20" height="14" viewBox="0 0 20 14"><rect x=".5" y=".5" width="19" height="13" fill="#f4f4f4" stroke="#aaa"/><path d="M1 1l9 7 9-7" fill="none" stroke="#aaa"/></svg>
    <span>info@fernlinkengineering.example</span>
  </div>
  <div class="abs btn-contact">CONTACT</div>
  <nav class="abs nav">
    <span class="nav-item active">LUMAFERNSITES HOME</span>
    <span class="nav-item" style="left:243px">TELEPHONE VOIP&nbsp; SOLUTION</span>
    <span class="nav-sep" style="left:379px"></span>
    <span class="nav-item" style="left:400px">IP, LAN AND INTERNET</span>
    <span class="nav-sep" style="left:511px"></span>
    <span class="nav-item" style="left:533px">SUPPORT SERVICES</span>
    <span class="nav-sep" style="left:634px"></span>
    <span class="nav-item" style="left:654px">CONTACT US</span>
  </nav>
  <div class="abs search">Search</div>
</header>

<section>
  <div class="abs slider" role="img" aria-label="Photo of a desk video phone showing a caller on its screen"></div>
  <div class="abs caption">
    <h2>LOREM IPSUM DOLOR SIT AMET, ELIT</h2>
    <p>Cum sociis natoque penatibus et magnis dis parturient montes, nascetur ridiculus mus. In iaculis facilisis massa. Etiam eu urna. Sed porta.Cum sociis natoque penatibus et magnis dis parturient montes.</p>
  </div>
  <div class="abs dots"><span></span><span></span><span></span><span></span></div>
</section>

<aside>
  <div class="abs panel quick"></div>
  <svg class="abs env" width="40" height="30" viewBox="0 0 40 30"><path d="M3 12L24 2l14 14-21 11z" fill="#fff"/><path d="M3 12l17 6 18-2" fill="none" stroke="#ccc"/></svg>
  <div class="abs quick-title">QUICK CONTACT</div>
  <div class="abs quick-rule"></div>
  <div class="field" style="top:563px">First Name</div>
  <div class="field" style="top:602px">Last Name</div>
  <div class="field" style="top:640px">Email</div>
  <div class="field" style="top:679px">Phone</div>
  <div class="field" style="top:717px;height:46px;padding-top:16px">Comments</div>
  <div class="abs captcha">
    <div class="captcha-words" role="img" aria-label="Distorted verification words"></div>
    <div class="captcha-entry">Type the two words<div></div></div>
  </div>
  <div class="abs btn-submit">SUBMIT</div>

  <div class="abs panel signup"></div>
  <div class="abs signup-title">Sign Up to Stay in Touch</div>
  <div class="abs signup-text">Please enter your email address below to sign up for our mailing list.</div>
  <div class="abs signup-input">your email address here..</div>
  <div class="abs btn-subscribe">Subscribe ›</div>
</aside>

<main>
  <div class="abs main"></div>
  <h1 class="abs welcome-title">WELCOME TO LUMAFERN <span>SITES</span></h1>
  <div class="abs welcome-img" role="img" aria-label="Monitor with a desk IP phone in front"></div>
  <div class="abs welcome-text">
    <p>LumaFernSites provides complete telephone VoIP PBX solutions for businesses large and small.</p>
    <p>Our team of telecom engineers will design and install the best business telephone VoIP PBX solution for your requirements. System features include: standard and advanced PBX call control actions, video telephone calling, toll free calling any where in the world, and 24x7 support.</p>
    <p>For more details, <a href="#">click here</a></p>
  </div>
  <div class="abs more-text">We also provide complete wired and wireless LAN/WAN/IP solutions and services for data, voice, Internet and private intranet networks to a variety of industries, including hospitality, industrial, commercial and institutional groups.<br>Our Support Services Division call center provides 24 x 7 help desk technical support services for industries including telecommunications, commercial and lodging / hotel.</div>
  <div class="abs btn-more one">learn more</div>

  <h2 class="abs sub-title why-title">WHY LUMAFERNSITES?</h2>
  <div class="abs why-img" role="img" aria-label="Stacked rack-mounted PBX units"></div>
  <div class="abs why-text">LumaFernSites provides state of the art VoIP PBX phone solutions with products tailored to small, medium, and large businesses.</div>
  <div class="abs btn-more two">learn more</div>

  <h2 class="abs sub-title ip-title">IP, LAN AND INTERNET</h2>
  <ul class="abs ip-list">
    <li>WIRED/WIRELESS INTERNET/INTRANET NETWORKS</li>
    <li>SECURE VPN NETWORKS</li>
    <li>RELIABLE INTERNET</li>
    <li>MULTI-MEDIA INTERFACING</li>
    <li>MEDIA EQUIPMENT RENTAL</li>
  </ul>
</main>

<footer>
  <div class="abs footer"></div>
  <div class="abs social">
    <span style="background:#3b5b9a"></span>
    <span style="background:#2ba3dc"></span>
    <span style="background:#333"></span>
    <span style="background:#f29a1f"></span>
    <span style="background:#c4181c"></span>
    <span style="background:#8fa3b8"></span>
  </div>
  <div class="abs copy">© 2013 lumafernsites., All Rights Reserved</div>
</footer>
</body>
</html>
```